School Communication Email Template

Looking for a designer to create a couple simple email templates that are matching our brand colors and feel. Attached is the default email template that is currently being sent out. Company details can be shared upon request.

Template is to be used within the booking tool we use (snapshot below) and gmail. Template code is in HTML (see screenshot below).
Updates

Template code for website should be in HTML. Sorry if that created confusion.

Target Market(s)

Parents of kids enrolled in our classes

Industry/Entity Type

Kids sport classes

Font styles to use
Serif

Colors
0054AA
0677BA
7BADD7
CADEEF
E8F1F8
FFF300
FFF600
FEFA6F
FFFEC7
FFFEE8

Requirements
Must have
• Consistency with company brand/colors
Nice to have
• Flexibility to be adjusted as needed

```html
<!DOCTYPE html>
<html lang="en">
<head>
<meta charset="utf-8">
<title>Booking Confirmation</title>
<link rel="stylesheet" href="https://fonts.googleapis.com/css2?family=Poppins:wght@400;500;600;700&display=swap">
<style>
  :root {
    --page-bg: #ffffff;
    --panel-bg: #243d85;
    --brand-yellow: #fbbf24;
    --text-dark: #3f3f46;
    --field-text: #1f2937;
    --field-bg: #ffffff;
    --field-border: #1a2a5c;
    --icon-color: #243d85;
    --white: #ffffff;
  }
  * { box-sizing: border-box; margin: 0; padding: 0; }
  html, body {
    width: 1200px;
    height: 852px;
    overflow: hidden;
    background: var(--page-bg);
    font-family: "Poppins", sans-serif;
  }
  .email {
    position: relative;
    width: 1200px;
    height: 852px;
  }
  .brand {
    position: absolute;
    top: 48px;
    left: 0;
    width: 100%;
    display: flex;
    justify-content: center;
    align-items: center;
    gap: 14px;
  }
  .brand-dot {
    width: 30px;
    height: 30px;
    border-radius: 50%;
    background: var(--brand-yellow);
  }
  .brand-name {
    font-size: 34px;
    font-weight: 600;
    color: var(--panel-bg);
    line-height: 1;
  }
  .greeting {
    position: absolute;
    top: 160px;
    left: 0;
    width: 100%;
    text-align: center;
    font-size: 29px;
    font-weight: 500;
    color: var(--text-dark);
    line-height: 40px;
  }
  .booking-panel {
    position: absolute;
    left: 93px;
    top: 217px;
    width: 1015px;
    height: 516px;
    background: var(--panel-bg);
    border-radius: 12px;
    box-shadow: 0 4px 12px rgba(0, 0, 0, 0.18);
  }
  .booking-title {
    position: absolute;
    top: 40px;
    left: 0;
    width: 100%;
    text-align: center;
    font-size: 40px;
    font-weight: 600;
    color: var(--white);
    line-height: 50px;
  }
  .form-row {
    position: absolute;
    left: 76.5px;
    width: 856.5px;
    display: grid;
    column-gap: 22.5px;
  }
  .form-row.two-col { grid-template-columns: 417px 417px; }
  .form-row.four-col {
    grid-template-columns: 198px 198px 198px 198px;
    column-gap: 21.5px;
  }
  .row-names { top: 120px; }
  .row-service { top: 236px; }
  .row-schedule { top: 358px; }
  .field-label {
    display: block;
    padding-left: 30px;
    font-size: 19px;
    font-weight: 600;
    color: var(--white);
    line-height: 20px;
    margin-bottom: 9px;
  }
  .row-schedule .field-label { padding-left: 30px; margin-bottom: 6.5px; }
  .field-input {
    position: relative;
    height: 58.5px;
    background: var(--field-bg);
    border: 1.5px solid var(--field-border);
    border-radius: 30px;
    box-shadow: 0 2px 4px rgba(0, 0, 0, 0.25);
    display: flex;
    align-items: center;
    padding-left: 44px;
    font-size: 17px;
    font-weight: 400;
    color: var(--field-text);
  }
  .four-col .field-input { padding-left: 42px; font-size: 16px; }
  .field-icon {
    position: absolute;
    top: 50%;
    transform: translateY(-50%);
    color: var(--icon-color);
  }
  .icon-chevron { right: 30px; width: 18px; height: 12px; }
  .icon-calendar, .icon-clock { right: 22px; width: 26px; height: 26px; }
  .footer-note {
    position: absolute;
    top: 772px;
    left: 0;
    width: 100%;
    text-align: center;
    font-size: 19px;
    font-weight: 400;
    color: var(--text-dark);
    line-height: 28px;
  }
</style>
</head>
<body>
<main class="email">
  <header class="brand">
    <span class="brand-dot"></span>
    <span class="brand-name">Brightstep Kids</span>
  </header>

  <p class="greeting">Dear, Mara Delwyn</p>

  <section class="booking-panel">
    <h1 class="booking-title">Booking</h1>

    <div class="form-row two-col row-names">
      <div class="form-field">
        <span class="field-label">Student First Name</span>
        <div class="field-input">Ollie</div>
      </div>
      <div class="form-field">
        <span class="field-label">Student Last Name</span>
        <div class="field-input">Penhallow</div>
      </div>
    </div>

    <div class="form-row two-col row-service">
      <div class="form-field">
        <span class="field-label">Appointment Name</span>
        <div class="field-input">Rosa Whitmore
          <svg class="field-icon icon-chevron" viewBox="0 0 18 12" fill="none" stroke="currentColor" stroke-width="2.4" stroke-linecap="round" stroke-linejoin="round"><path d="M2 2l7 7 7-7"/></svg>
        </div>
      </div>
      <div class="form-field">
        <span class="field-label">Service</span>
        <div class="field-input">Swimming
          <svg class="field-icon icon-chevron" viewBox="0 0 18 12" fill="none" stroke="currentColor" stroke-width="2.4" stroke-linecap="round" stroke-linejoin="round"><path d="M2 2l7 7 7-7"/></svg>
        </div>
      </div>
    </div>

    <div class="form-row four-col row-schedule">
      <div class="form-field">
        <span class="field-label">Start Date</span>
        <div class="field-input">15.01.2023
          <svg class="field-icon icon-calendar" viewBox="0 0 24 24" fill="none" stroke="currentColor" stroke-width="1.5"><rect x="3" y="5" width="18" height="16" rx="1.5"/><path d="M3 9.5h18M8 3v4M16 3v4"/><path d="M7 13h2M11 13h2M15 13h2M7 16.5h2M11 16.5h2M15 16.5h2" stroke-width="1.8"/></svg>
        </div>
      </div>
      <div class="form-field">
        <span class="field-label">End Date</span>
        <div class="field-input">20.01.2023
          <svg class="field-icon icon-calendar" viewBox="0 0 24 24" fill="none" stroke="currentColor" stroke-width="1.5"><rect x="3" y="5" width="18" height="16" rx="1.5"/><path d="M3 9.5h18M8 3v4M16 3v4"/><path d="M7 13h2M11 13h2M15 13h2M7 16.5h2M11 16.5h2M15 16.5h2" stroke-width="1.8"/></svg>
        </div>
      </div>
      <div class="form-field">
        <span class="field-label">Start Time</span>
        <div class="field-input">15:00:00
          <svg class="field-icon icon-clock" viewBox="0 0 24 24" fill="none" stroke="currentColor" stroke-width="1.5" stroke-linecap="round"><circle cx="12" cy="12" r="10"/><path d="M12 6v6l-3 4"/></svg>
        </div>
      </div>
      <div class="form-field">
        <span class="field-label">End Time</span>
        <div class="field-input">17:00:00
          <svg class="field-icon icon-clock" viewBox="0 0 24 24" fill="none" stroke="currentColor" stroke-width="1.5" stroke-linecap="round"><circle cx="12" cy="12" r="10"/><path d="M12 6v6l-3 4"/></svg>
        </div>
      </div>
    </div>
  </section>

  <footer class="footer-note">©2023. All rights reserved.</footer>
</main>
</body>
</html>
```